Corporate Business Card

Very professional, Modern, Not to busy, include phone address email, website
(555) 617-4930, 18761 52nd Avenue S, Alder Falls, OR 98047, martin@plumlinegroup.com, varkoworks.com

Target Market(s)

Manufacturing

Industry/Entity Type

Aero, machining, manufacturing, Off road racing

Contact Information for Business Card

Phone, address email, website

```html
<!DOCTYPE html>
<html lang="en">
<head>
<meta charset="utf-8">
<title>Varko Works – Business Card</title>
<link href="https://fonts.googleapis.com/css2?family=Montserrat:wght@400;500;700&display=swap" rel="stylesheet">
<style>
  :root {
    --navy: #16366f;
    --red: #d2232a;
    --white: #ffffff;
    --ink: #1b1b1b;
    --backdrop: #6b6b6b;
  }
  * { margin: 0; padding: 0; box-sizing: border-box; }
  html, body {
    width: 1200px; height: 801px; overflow: hidden;
    background: var(--backdrop);
    font-family: "Montserrat", sans-serif;
  }
  .sheet {
    position: relative; width: 1200px; height: 801px;
    display: flex; align-items: center; justify-content: center; gap: 50px;
  }
  .card {
    position: relative; width: 525px; height: 300px; overflow: hidden;
    box-shadow: 0 18px 36px rgba(0,0,0,.35);
  }
  /* front */
  .card-front { background: var(--white); border-bottom: 3px solid var(--red); }
  .front-brand {
    position: absolute; left: 34px; top: 112px; width: 190px;
    font-weight: 700; font-size: 30px; line-height: 1.05; color: var(--navy);
    letter-spacing: .5px;
  }
  .front-divider {
    position: absolute; left: 232px; top: 46px; width: 1.5px; height: 170px;
    background: var(--red);
  }
  .contact { position: absolute; left: 254px; top: 40px; color: var(--ink); }
  .contact-name {
    font-weight: 700; font-size: 21px; color: var(--red);
    letter-spacing: .5px; text-transform: uppercase;
  }
  .contact-title { font-size: 13px; margin-top: 2px; }
  .contact-address { font-size: 13px; line-height: 1.4; margin-top: 14px; }
  .contact-lines { list-style: none; margin-top: 12px; font-size: 13px; line-height: 1.55; }
  .contact-lines li { display: flex; align-items: center; gap: 6px; }
  .contact-lines svg { width: 12px; height: 12px; flex: none; }
  .front-band { position: absolute; left: 0; bottom: 0; width: 525px; height: 60px; }
  /* back */
  .card-back {
    background: var(--navy); border-bottom: 3px solid var(--red);
    display: flex; align-items: center; justify-content: center;
  }
  .back-brand {
    font-weight: 700; font-size: 54px; color: var(--white); letter-spacing: 1px;
  }
</style>
</head>
<body>
<main class="sheet">
  <section class="card card-front" aria-label="Business card front">
    <div class="front-brand">Varko Works</div>
    <div class="front-divider"></div>
    <div class="contact">
      <p class="contact-name">Daniel Reyes</p>
      <p class="contact-title">Owner/CEO</p>
      <p class="contact-address">4410, 18761 52nd<br>Avenue S, Alder Falls, OR 98047</p>
      <ul class="contact-lines">
        <li>
          <svg viewBox="0 0 12 12" aria-hidden="true"><path fill="var(--red)" d="M3 1l2 2.4-1.2 1.3a6 6 0 0 0 3.5 3.5L8.6 7 11 9l-1.4 1.7C5.6 10.4 1.6 6.4 1.3 2.4z"/></svg>
          (555) 617-4930
        </li>
        <li>
          <svg viewBox="0 0 12 12" aria-hidden="true"><rect x="1" y="2.5" width="10" height="7" fill="var(--red)"/><path d="M1 2.5l5 4 5-4" stroke="#fff" fill="none" stroke-width="1"/></svg>
          martin@plumlinegroup.com
        </li>
        <li>
          <svg viewBox="0 0 12 12" aria-hidden="true"><circle cx="6" cy="6" r="5" fill="var(--red)"/><path d="M1 6h10M6 1c-2.5 3-2.5 7 0 10M6 1c2.5 3 2.5 7 0 10" stroke="#fff" fill="none" stroke-width=".8"/></svg>
          www.varkoworks.com
        </li>
      </ul>
    </div>
    <svg class="front-band" viewBox="0 0 525 60" preserveAspectRatio="none" aria-hidden="true">
      <polygon points="0,50 260,50 268,40 0,40" fill="var(--red)"/>
      <polygon points="0,60 525,60 525,0 300,0 292,26 270,52 0,52" fill="var(--navy)"/>
      <polygon points="0,52 270,52 268,54 0,54" fill="var(--white)"/>
    </svg>
  </section>

  <section class="card card-back" aria-label="Business card back">
    <div class="back-brand">Varko Works</div>
  </section>
</main>
</body>
</html>
```